EXCITING DECK for Automotive dealers that shows how our Technology works.

General Concept
The deck should visually represent the Trade and Credit Lead Life Cycle program is a dynamic, interconnected journey, illustrating how leads are generated, nurtured, and converted. The focus should be on how your system flows seamlessly between credit and trade-in opportunities for consumers, with the goal of maximizing engagement and conversions.
Slide 1: Title Slide - Lead Life Cycle Program
• Visual Concept: A stylized cycle or wheel that represents the stages of the lead life cycle, with arrows connecting each stage.
• Headline: "Lead Life Cycle Program"
• Subhead line: "Credit Pre-Qualification and Trade-In Appraisal"
• Imagery: Modern, sleek graphics of vehicles, smartphones (for texting), email icons, and dollar signs for value.
Slide 2: Lead Generation Sources
• Visual Concept: A funnel with the top representing the different lead generation sources.
• Content:
o Top of Funnel (Leads Enter):
 Pre-Qualification Tool (Fast4Loan)- How it Works
 1. Converts Web Traffic into the highest quality lead on the market
 Vorqel Email/Mail Marketing – How it Works
 1. Delivers actionable leads from email marketing not Just OPENS AND CLICKS. Show the text demo. Audiences below
1. Past Sold Customers (Equity Targets)
2. Past Service Onlu Department Customers (Conquest Sales)
3. Unsold Leads (from previous interactions)
o Each source should have a distinct icon to represent it (e.g., envelope for email, a wrench for past service customers, etc.).
• Headline: "Multiple Lead Sources Feeding into the Program"
• Imagery: The funnel narrowing toward the next step with leads symbolized by icons flowing downward.
Slide 3: Credit Leads - Pre-Qualified Flow
• Visual Concept: A customer engaging with the Fast4Loan tool on their mobile, being pre-qualified, and then us sending a offer to appraise their trade.
• Flow Explanation:
o Customer pre-qualifies via Fast4Loan → Receives credit approval → Email and Mail Example to check trade-in value.
• Headline: "Pre-Qualified Leads: Offering Trade-In Appraisal"
• Imagery: A sequence that shows how a customer moves from pre-qualification to considering their trade-in value. To purchasing
Slide 4: Trade-In Leads - Valuation Flow
• Visual Concept: A customer who has received a trade-in valuation offer now being prompted to pre-qualify for financing.
• Flow Explanation:
o Customer texts for vehicle value → Receives trade-in appraisal → Offer to pre-qualify for financing appears link is at the bottom of the text response.
• Headline: "Trade-In Leads: Offering Credit Pre-Qualification"
• Imagery: A customer looking at their trade-in value on their phone and being shown an additional prompt to pre-qualify for a loan.
Slide 5: Cross-Offer Opportunities
• Visual Concept: A two-way street or cycle, illustrating the seamless transition between offering pre-qualification to trade-in customers and offering trade-in value to credit leads.
• Content:
o Two pathways:
1. Start as a Credit Lead → Offer Trade-In Valuation
2. Start as a Trade-In Lead → Offer Credit Pre-Qualification
o Headline: "Cross-Offer Opportunities for Maximum Engagement"
• Imagery: Arrows going in both directions, symbolizing the back-and-forth opportunities between credit and trade leads.
Digital Retargeting for Cross-Action Engagement
• Visual Concept: An omnichannel approach with a customer in the center, surrounded by email/Mail icons, Chatterbook, and Snapgrove logos. Arrows leading from each platform back to the customer, showing how these channels drive engagement.
• Content:
o Title: "Engage to Convert one lead type to get both with Email/Mail and Digital Retargeting"
o Explanation:
 Whether a lead starts as a Pre-Qualified Credit Lead or a Trade-In Valuation Lead, we use personalized Email/Mail Campaigns and Digital Retargeting Ads (Chatterbook & Snapgrove) to encourage them to take the next action.
 If they pre-qualify for credit, we retarget them with trade-in valuation offers.
 If they start with a trade-in valuation, we follow up with financing offers.
o Headline: "Leverage Email & Social Retargeting to Drive Cross-Action"
• Visuals:
o Icons of Email, Chatterbook, and Snapgrove: Showing the platforms through which you retarget leads.
o Customer Journey Map: Illustrating how leads who interacted once are guided to the next step (credit lead → trade-in offer, trade-in lead → pre-qualification).
o Arrows Flowing Between Channels: Showing how no matter where a lead starts, they are continually engaged through digital touchpoints until they complete both actions.
o Ad examples
• Call to Action: "Stay Top of Mind and Convert Leads into Multi-Action Customers"
This slide emphasizes how you’re leveraging both email/mail marketing and social media retargeting to move leads further along the customer journey, regardless of how they entered your funnel. The visuals should reinforce the idea of continuous engagement and omnipresent reminders for them to take action.
________________________________________
Slide 6: Lifecycle Representation
• Visual Concept: A circular diagram showing how leads can continuously move between credit and trade offers throughout their lifecycle.
• Content:
o Show how the lifecycle doesn’t end after one interaction, but can continue with follow-up offers.
o Headline: "Continuous Engagement Throughout the Lead Life Cycle"
• Imagery: Circular arrows or flowchart representing each stage looping back into the lifecycle, emphasizing that leads can be re-engaged.
Slide 7: Lead Conversion Goals
• Visual Concept: A progression from leads to successful transactions (e.g., a customer with keys to a new car). Showing that getting customers to take both of these actions delives a lead that is very committed to the process of buying.
• Content:
o End goal: Convert both credit and trade leads into sales.
o Show statistics or success metrics as optional data points.
o Headline: "Converting Leads into Sales"
• Imagery: A car dealership handing over keys, happy customers, and sold vehicles.
Slide 8: Next Steps / Call to Action
• Visual Concept: A final slide summarizing the key takeaways and next steps.
• Headline: "Maximize Lead Potential with Cross-Offer Opportunities"
• Imagery: A mix of credit leads, trade leads, and successful customer outcomes.
________________________________________These slides should be clean and modern, using simple but impactful visuals like arrows, icons, and flow diagrams to represent the journey. The key is to emphasize flow and interaction between credit and trade-in opportunities, showing the two-way cross-sell nature of your Lead Life Cycle Program.

I have attached a current deck so you can pull some basic product info and graphics into the new deck (PLEASE DONT JUST COPY THE OLD DECK). I have also included some of our email artwrok if you need it. If you want to look at our website go here www.plorvenadsgroup.example

Target Market(s)

Car Dealers

Industry/Entity Type

Automotive Marketing

Requirements
Must have
• PLEASE READ THE PROJECT DESCRIPTION
Nice to have
Should not have
• PLEASE dont just copy the deck i uploaded. I am looking for a differnt take.

```html
<!DOCTYPE html>
<html lang="en">
<head>
<meta charset="utf-8">
<title>Lead Life Cycle Program Deck</title>
<link rel="stylesheet" href="https://fonts.googleapis.com/css2?family=Michroma&family=Lato:wght@400;700&display=swap">
<style>
:root{
  --red:#e2001a;
  --dark:#3d3d3f;
  --ink:#1f1f1f;
  --muted:#555;
  --bg:#e4e4e4;
  --white:#fff;
}
*{box-sizing:border-box;margin:0;padding:0}
html,body{width:1032px;height:1200px;overflow:hidden;background:var(--bg)}
.canvas{position:relative;width:1032px;height:1200px;overflow:hidden;background:var(--bg);font-family:"Lato",sans-serif;color:var(--ink)}
.slide{position:absolute;width:765px;height:430px;background:var(--white);transform:scale(.5793);transform-origin:0 0;overflow:hidden;box-shadow:0 2px 6px rgba(0,0,0,.12)}
.col-l{left:40px}.col-r{left:536.6px}
.row-1{top:43.5px}.row-2{top:329px}.row-3{top:614.3px}.row-4{top:900px}
.frame{position:absolute;left:0;top:0}
.slide-title{position:absolute;left:34px;top:13px;font-family:"Michroma",sans-serif;font-size:15.5px;color:var(--white);letter-spacing:.3px}
.footer-page,.footer-copy{position:absolute;top:416px;font-size:7px;color:var(--white);font-weight:700}
.footer-page{left:34px}
.footer-copy{left:318px;font-weight:400}
.brand{position:absolute;left:672px;top:399px;display:flex;align-items:center;gap:4px;font-size:10px;font-weight:700;color:var(--ink)}
.brand i{display:block;width:7px;height:7px;background:var(--red)}
.abs{position:absolute}
.subtitle{font-size:16px;color:var(--ink);text-align:center;width:765px;left:0}
.stage-label{font-size:10.5px;line-height:16px;font-weight:700}
.stage-label b{color:var(--red);font-weight:400;display:block}
.r-align{text-align:right}
.icon{position:absolute;width:48px;height:48px;border-radius:50%;background:var(--red);border:3px solid #f6c3c9;display:flex;align-items:center;justify-content:center;box-shadow:0 2px 5px rgba(0,0,0,.2)}
.icon svg{width:24px;height:24px;stroke:var(--white);fill:none;stroke-width:1.6;stroke-linecap:round;stroke-linejoin:round}
.photo{position:absolute;background:linear-gradient(135deg,#c9c5c0,#8e8a86)}
.photo.round{border-radius:50%}
.ring{position:absolute;border-radius:50%;border:3px solid var(--red)}
.dash{position:absolute;border-top:1.5px dashed var(--dark)}
.dash.v{border-top:0;border-left:1.5px dashed var(--dark)}
.col-head{font-size:10.5px;font-weight:700;text-align:center;line-height:19px}
.small{font-size:9px;color:var(--muted);line-height:16px;text-align:center}
.small em{font-style:normal;color:var(--red);font-weight:700}
.funnel{position:absolute;width:174px;height:152px;clip-path:polygon(0 0,100% 0,58% 40%,56% 100%,43% 92%,42% 40%);background:linear-gradient(160deg,#d8d6d2,#6f6a66)}
.list-row{position:absolute;display:flex;align-items:center;gap:14px;font-size:9.5px;color:var(--muted)}
.list-row .icon{position:static;flex:none}
.lead{font-size:11.5px;font-weight:700}
.bubble{position:absolute;background:var(--white);border-radius:16px;box-shadow:0 2px 8px rgba(0,0,0,.18);font-size:9px;text-align:center;line-height:17px;padding:8px 14px}
.pill{position:absolute;background:var(--white);border-radius:12px;font-size:7.5px;font-weight:700;padding:6px 12px;box-shadow:0 2px 6px rgba(0,0,0,.2);display:flex;align-items:center;gap:4px}
.pill i{display:block;width:6px;height:6px;background:var(--red);border-radius:50%}
.price{position:absolute;background:var(--white);border:1.5px solid #e6a300;border-radius:10px;font-size:6.5px;color:#e6a300;padding:2px 5px}
.tag{position:absolute;background:var(--white);border-radius:6px;font-size:15px;font-weight:700;color:var(--dark);padding:4px 10px}
.vertical{position:absolute;font-size:9px;line-height:12px;text-align:center;white-space:nowrap}
.arrow-dot{position:absolute;width:18px;height:18px;border-radius:50%;background:var(--white);color:var(--red);font-size:11px;line-height:17px;text-align:center;box-shadow:0 1px 3px rgba(0,0,0,.25)}
.red-dot{position:absolute;width:22px;height:22px;border-radius:50%;background:var(--red);border:2px solid var(--white);box-shadow:0 1px 3px rgba(0,0,0,.25);display:flex;align-items:center;justify-content:center}
.red-dot svg{width:11px;height:11px;stroke:var(--white);fill:none;stroke-width:1.6}
.flow{font-size:9px;color:var(--muted);text-align:center;width:200px;line-height:21px}
.flow span{color:var(--red)}
.cta{font-size:8px;color:var(--red);text-decoration:underline;text-align:center;width:200px;line-height:14px}
.para{font-size:10px;color:var(--muted);line-height:20px;width:335px}
.stat{position:absolute;top:283px;text-align:left}
.stat b{display:block;font-family:"Michroma",sans-serif;font-size:20px;color:var(--red);font-weight:400}
.stat span{display:block;font-size:11px;margin-top:8px}
.start{color:var(--red);font-size:11px;text-align:center}
</style>
</head>
<body>
<div class="canvas">

<!-- SHARED FRAME: header + footer drawn in each slide -->

<!-- Slide 1 -->
<section class="slide col-l row-1">
  <svg class="frame" width="765" height="430"><polygon points="0,0 648,0 620,46 0,46" fill="#e2001a"/><polygon points="660,0 765,0 765,46 634,46" fill="#3d3d3f"/><polygon points="0,46 405,46 395,58 0,58" fill="#3d3d3f"/><polygon points="0,412 590,412 610,430 0,430" fill="#e2001a"/></svg>
  <h1 class="slide-title">LEAD LIFE CYCLE PROGRAM</h1>
  <p class="abs subtitle" style="top:78px">Credit Pre-Qualification and Trade-In Appraisal</p>
  <div class="dash v" style="left:383px;top:160px;height:24px"></div>
  <div class="dash" style="left:243px;top:285px;width:36px"></div>
  <div class="dash" style="left:488px;top:285px;width:36px"></div>
  <div class="ring" style="left:277px;top:179px;width:212px;height:212px"></div>
  <div class="photo round" role="img" aria-label="Photo of a bicycle against a concrete wall" style="left:285px;top:187px;width:196px;height:196px"></div>
  <div class="icon" style="left:360px;top:113px"><svg viewBox="0 0 24 24"><path d="M4 11h4v9H4zM8 11l4-7c2 0 2 2 1 4h6c1 0 2 1 1 3l-2 7c0 1-1 2-2 2H8"/></svg></div>
  <div class="abs stage-label" style="left:423px;top:120px"><b>STAGE 02</b>Receives Credit Approval</div>
  <div class="icon" style="left:195px;top:261px"><svg viewBox="0 0 24 24"><rect x="3" y="6" width="18" height="12" rx="2"/><path d="M3 10h18M6 15h5"/></svg></div>
  <div class="abs stage-label r-align" style="left:80px;top:268px;width:100px"><b>STAGE 01</b>Fast4Loan</div>
  <div class="icon" style="left:524px;top:261px"><svg viewBox="0 0 24 24"><rect x="3" y="6" width="18" height="13" rx="1"/><path d="M3 7l9 7 9-7"/></svg></div>
  <div class="abs stage-label" style="left:586px;top:268px"><b>STAGE 03</b>Email and Mail</div>
  <div class="footer-page">PAGE | 01</div><div class="footer-copy">© 2024 Plorven Marketing | All Rights Reserved</div>
  <div class="brand"><i></i>Plorven</div>
</section>

<!-- Slide 2 -->
<section class="slide col-r row-1">
  <svg class="frame" width="765" height="430"><polygon points="0,0 648,0 620,46 0,46" fill="#e2001a"/><polygon points="660,0 765,0 765,46 634,46" fill="#3d3d3f"/><polygon points="0,46 405,46 395,58 0,58" fill="#3d3d3f"/><polygon points="0,412 590,412 610,430 0,430" fill="#e2001a"/></svg>
  <h1 class="slide-title">LEAD GENERATION SOURCES</h1>
  <p class="abs col-head" style="left:23px;top:103px;width:220px">Pre-Qualification Tool - How it Works</p>
  <p class="abs col-head" style="left:275px;top:103px;width:220px">Vorqel Email – How it Works</p>
  <p class="abs col-head" style="left:510px;top:103px;width:252px">Multiple Lead Sources Feeding into the Program</p>
  <div class="funnel" role="img" aria-label="Funnel-shaped photo of a team at work" style="left:47px;top:134px"></div>
  <div class="funnel" role="img" aria-label="Funnel-shaped photo of colleagues reviewing documents" style="left:298px;top:134px"></div>
  <div class="funnel" role="img" aria-label="Funnel-shaped photo of a meeting room" style="left:549px;top:134px"></div>
  <p class="abs small" style="left:33px;top:291px;width:200px">Converts Web Traffic into the highest<br>quality lead on the market</p>
  <p class="abs small" style="left:265px;top:291px;width:240px"><em>01.</em> Past Sold Customers<br><span style="line-height:20px"><em>02.</em> Past Service Onlu Department Customers</span><br><em>03.</em> Unsold Leads</p>
  <div class="red-dot" style="left:625px;top:258px"><svg viewBox="0 0 12 12"><path d="M6 2v6M3 5l3 3 3-3M2 10h8"/></svg></div>
  <svg class="abs" style="left:628px;top:297px" width="16" height="12" viewBox="0 0 16 12" fill="none" stroke="#e2001a" stroke-width="1.2"><rect x="1" y="1" width="14" height="10"/><path d="M1 1l7 6 7-6"/></svg>
  <p class="abs small" style="left:536px;top:312px;width:200px;color:#333">Envelope for email</p>
  <svg class="abs" style="left:626px;top:338px" width="20" height="18" viewBox="0 0 20 18" fill="none" stroke="#e2001a" stroke-width="1.2"><circle cx="6" cy="5" r="2.5"/><circle cx="14" cy="5" r="2.5"/><path d="M2 12c0-3 8-3 8 0M10 12c0-3 8-3 8 0M3 16h14"/></svg>
  <p class="abs small" style="left:516px;top:361px;width:240px;color:#333">A Wrench For Past Service Customer</p>
  <div class="footer-page">PAGE | 02</div><div class="footer-copy">© 2024 Plorven Marketing | All Rights Reserved</div>
  <div class="brand"><i></i>Plorven</div>
</section>

<!-- Slide 3 -->
<section class="slide col-l row-2">
  <svg class="frame" width="765" height="430"><polygon points="0,0 648,0 620,46 0,46" fill="#e2001a"/><polygon points="660,0 765,0 765,46 634,46" fill="#3d3d3f"/><polygon points="0,46 405,46 395,58 0,58" fill="#3d3d3f"/><polygon points="0,412 590,412 610,430 0,430" fill="#e2001a"/></svg>
  <h1 class="slide-title">CREDIT LEADS - PRE-QUALIFIED FLOW</h1>
  <p class="abs lead" style="left:34px;top:127px">Pre-Qualified Leads: Offering Trade-In Appraisal</p>
  <div class="list-row" style="left:33px;top:155px"><div class="icon"><svg viewBox="0 0 24 24"><circle cx="12" cy="10" r="6"/><path d="M9 10l2 2 4-4M9 16l-2 5M15 16l2 5"/></svg></div>Customer pre-qualifies via Fast4Loan</div>
  <div class="list-row" style="left:33px;top:215px"><div class="icon"><svg viewBox="0 0 24 24"><rect x="4" y="9" width="16" height="11" rx="1"/><path d="M9 3v5M7 6l2 2 2-2M4 13h16"/></svg></div>Receives credit approval</div>
  <div class="list-row" style="left:33px;top:275px"><div class="icon"><svg viewBox="0 0 24 24"><path d="M3 8h8M3 11h6M4 14l5 4 4-3 7 3M13 9l7-2"/></svg></div>Email and Mail Example to check trade-in value</div>
  <div class="photo" role="img" aria-label="Photo of young people seated on a bench using their phones" style="left:382px;top:93px;width:348px;height:270px;border-radius:14px;background:linear-gradient(180deg,#e7e5e8,#9c8f86 55%,#c5a473)"></div>
  <div class="tag" style="left:585px;top:102px">Fast4Loan</div>
  <div class="bubble" style="left:378px;top:82px;width:186px">Pre-qualification To Considering<br>Their Trade-in Value</div>
  <div class="footer-page">PAGE | 03</div><div class="footer-copy">© 2024 Plorven Marketing | All Rights Reserved</div>
  <div class="brand"><i></i>Plorven</div>
</section>

<!-- Slide 4 -->
<section class="slide col-r row-2">
  <svg class="frame" width="765" height="430"><polygon points="0,0 648,0 620,46 0,46" fill="#e2001a"/><polygon points="660,0 765,0 765,46 634,46" fill="#3d3d3f"/><polygon points="0,46 405,46 395,58 0,58" fill="#3d3d3f"/><polygon points="0,412 590,412 610,430 0,430" fill="#e2001a"/></svg>
  <h1 class="slide-title">TRADE-IN LEADS - VALUATION FLOW</h1>
  <div class="abs" style="left:33px;top:106px;width:284px;height:284px;border-radius:50%;background:#f7c9ce"></div>
  <div class="photo round" role="img" aria-label="Photo of a smiling man checking his trade-in value on a phone" style="left:40px;top:112px;width:272px;height:272px;background:radial-gradient(circle at 50% 60%,#d8dde6 0 30%,#e2001a 31%)"></div>
  <div class="pill" style="left:229px;top:142px"><i></i>PRE-QUALIFY FOR A LOAN</div>
  <div class="price" style="left:187px;top:232px">$ 2,00,000</div>
  <p class="abs lead" style="left:471px;top:127px">Trade-In Leads: Offering Credit Pre-Qualification</p>
  <div class="list-row" style="left:470px;top:155px"><div class="icon"><svg viewBox="0 0 24 24"><rect x="5" y="4" width="14" height="16" rx="1"/><path d="M8 8h8M8 12h8M8 16h5"/></svg></div>Customer texts for vehicle value</div>
  <div class="list-row" style="left:470px;top:215px"><div class="icon"><svg viewBox="0 0 24 24"><rect x="5" y="3" width="12" height="18" rx="1"/><path d="M8 7h6M8 11h6M8 15h3M16 14l4-4"/></svg></div>Receives trade-in appraisal</div>
  <div class="list-row" style="left:470px;top:275px;line-height:19px"><div class="icon"><svg viewBox="0 0 24 24"><circle cx="8" cy="8" r="2.5"/><circle cx="16" cy="8" r="2.5"/><path d="M4 14c0-3 8-3 8 0M12 14c0-3 8-3 8 0M4 18c4 2 12 2 16-2"/></svg></div>Offer to pre-qualify for financing appears link<br>is at the bottom of the text response.</div>
  <div class="footer-page">PAGE | 04</div><div class="footer-copy">© 2024 Plorven Marketing | All Rights Reserved</div>
  <div class="brand"><i></i>Plorven</div>
</section>

<!-- Slide 5 -->
<section class="slide col-l row-3">
  <svg class="frame" width="765" height="430"><polygon points="0,0 648,0 620,46 0,46" fill="#e2001a"/><polygon points="660,0 765,0 765,46 634,46" fill="#3d3d3f"/><polygon points="0,46 405,46 395,58 0,58" fill="#3d3d3f"/><polygon points="0,412 590,412 610,430 0,430" fill="#e2001a"/></svg>
  <h1 class="slide-title">CROSS-OFFER OPPORTUNITIES</h1>
  <p class="abs col-head" style="left:43px;top:78px;width:200px">Cross-Offer Opportunities for<br>Maximum Engagement</p>
  <p class="abs col-head" style="left:298px;top:78px;width:200px">Digital Retargeting for Cross<br>Action Engagement</p>
  <p class="abs col-head" style="left:522px;top:78px;width:220px">Leverage Email &amp; Social Retargeting<br>to Drive Cross-Action</p>
  <div class="photo round" role="img" aria-label="Photo of colleagues planning with sticky notes" style="left:77px;top:131px;width:132px;height:132px"></div>
  <div class="arrow-dot" style="left:67px;top:188px">←</div>
  <div class="arrow-dot" style="left:205px;top:188px">→</div>
  <div class="vertical" style="left:10px;top:184px;transform:rotate(-90deg)">Offer Credit<br>Pre-Qualification</div>
  <div class="vertical" style="left:215px;top:184px;transform:rotate(90deg)">Offer Trade In<br>Valuation</div>
  <p class="abs start" style="left:93px;top:277px;width:100px">START AS</p>
  <div class="photo round" role="img" aria-label="Photo of a young man with a backpack reading his phone" style="left:331px;top:139px;width:136px;height:136px;background:linear-gradient(135deg,#d9d9da,#8d8d90)"></div>
  <p class="abs small" style="left:289px;top:285px;width:220px">Engage to Convert one lead type to get both<br>with Mail and Digital Retargeting</p>
  <div class="abs" style="left:565px;top:139px;width:138px;height:138px;border-radius:50%;border:1.5px solid var(--dark);background:radial-gradient(circle at 50% 62%,#bfe3ef 0 35%,#fff 60%)" role="img" aria-label="Illustrated customer journey map"></div>
  <p class="abs" style="left:595px;top:160px;font-size:11px;font-weight:700;color:var(--dark)">Fast4Loan</p>
  <div class="red-dot" style="left:549px;top:141px"></div>
  <div class="red-dot" style="left:688px;top:131px"><svg viewBox="0 0 12 12"><rect x="1" y="2.5" width="10" height="7"/><path d="M1 2.5l5 4 5-4"/></svg></div>
  <div class="red-dot" style="left:541px;top:239px"></div>
  <div class="abs flow" style="left:535px;top:283px">Credit lead <span>⟶</span><br><span>⟶</span> Trade-in Offer, Trade-in Lead <span>⟶</span><br>Pre-Qualification</div>
  <p class="abs cta" style="left:535px;top:352px">Stay Top of Mind and Convert Leads into<br>Multi-Action Customers</p>
  <div class="footer-page">PAGE | 05</div><div class="footer-copy">© 2024 Plorven Marketing | All Rights Reserved</div>
  <div class="brand"><i></i>Plorven</div>
</section>

<!-- Slide 6 -->
<section class="slide col-r row-3">
  <svg class="frame" width="765" height="430"><polygon points="0,0 648,0 620,46 0,46" fill="#e2001a"/><polygon points="660,0 765,0 765,46 634,46" fill="#3d3d3f"/><polygon points="0,46 405,46 395,58 0,58" fill="#3d3d3f"/><polygon points="0,412 590,412 610,430 0,430" fill="#e2001a"/></svg>
  <h1 class="slide-title">LIFECYCLE REPRESENTATION</h1>
  <p class="abs subtitle" style="top:77px">Continuous Engagement Throughout the Lead Life Cycle</p>
  <div class="dash v" style="left:383px;top:154px;height:26px"></div>
  <div class="dash" style="left:243px;top:226px;width:46px"></div>
  <div class="dash" style="left:478px;top:226px;width:46px"></div>
  <div class="dash" style="left:243px;top:333px;width:36px"></div>
  <div class="dash" style="left:488px;top:333px;width:36px"></div>
  <div class="ring" style="left:277px;top:179px;width:212px;height:212px"></div>
  <div class="photo round" role="img" aria-label="Photo of a team presenting charts on a whiteboard" style="left:285px;top:187px;width:196px;height:196px;background:linear-gradient(135deg,#d8d3cd,#8a8177)"></div>
  <div class="icon" style="left:360px;top:106px"><svg viewBox="0 0 24 24"><rect x="4" y="4" width="16" height="12" rx="2"/><circle cx="12" cy="10" r="3"/><path d="M9 20h6"/></svg></div>
  <div class="abs stage-label" style="left:423px;top:113px"><b>STAGE 03</b>Lorem ipsum dolor</div>
  <div class="icon" style="left:195px;top:202px"><svg viewBox="0 0 24 24"><rect x="3" y="6" width="18" height="12" rx="2"/><path d="M3 10h18M6 15h5"/></svg></div>
  <div class="abs stage-label r-align" style="left:60px;top:209px;width:120px"><b>STAGE 02</b>Credit Offers</div>
  <div class="icon" style="left:524px;top:202px"><svg viewBox="0 0 24 24"><rect x="3" y="6" width="18" height="13" rx="1"/><path d="M3 7l9 7 9-7"/></svg></div>
  <div class="abs stage-label" style="left:586px;top:209px"><b>STAGE 04</b>Lorem ipsum dolor</div>
  <div class="icon" style="left:195px;top:309px"><svg viewBox="0 0 24 24"><path d="M4 20h16M7 17v-4M11 17V9M15 17v-6M19 17V6"/></svg></div>
  <div class="abs stage-label r-align" style="left:60px;top:316px;width:120px"><b>STAGE 01</b>Trade Offers</div>
  <div class="icon" style="left:524px;top:309px"><svg viewBox="0 0 24 24"><rect x="4" y="4" width="16" height="11" rx="2"/><path d="M8 19l3-4h5M8 8h8M8 11h5"/></svg></div>
  <div class="abs stage-label" style="left:586px;top:316px"><b>STAGE 05</b>Lorem ipsum dolor</div>
  <div class="footer-page">PAGE | 06</div><div class="footer-copy">© 2024 Plorven Marketing | All Rights Reserved</div>
  <div class="brand"><i></i>Plorven</div>
</section>

<!-- Slide 7 -->
<section class="slide col-l row-4">
  <svg class="frame" width="765" height="430"><polygon points="0,0 648,0 620,46 0,46" fill="#e2001a"/><polygon points="660,0 765,0 765,46 634,46" fill="#3d3d3f"/><polygon points="0,46 405,46 395,58 0,58" fill="#3d3d3f"/><polygon points="0,412 590,412 610,430 0,430" fill="#e2001a"/></svg>
  <h1 class="slide-title">LEAD CONVERSION GOALS</h1>
  <div class="abs" style="left:35px;top:152px;width:242px;height:226px;background:var(--red)"></div>
  <div class="photo" role="img" aria-label="Photo of a salesman handing car keys to a happy customer" style="left:54px;top:87px;width:298px;height:271px;background:linear-gradient(135deg,#e6e6e6,#8b8f95)"></div>
  <p class="abs" style="left:405px;top:110px;font-size:16px">Converting Leads into Sales</p>
  <p class="abs para" style="left:405px;top:135px">Lorem ipsum dolor sit amet, consectetur adipiscing elit, sed do eius-mod tempor incididunt ut labore et dolore magna aliqua. Ut enim ad minim veniam, quis nostrud exercitation ullamco laboris nisi ut aliquip ex ea commodo consequat. Duis aute irure dolor in reprehenderit in voluptate velit esse cillum dolore eu fugiat nulla pariatur. Excepteur sint occaecat cupidatat non proident, sunt in culpa qui officia deserunt mollit anim id est laborum.</p>
  <div class="stat" style="left:405px"><b>60</b><span>Lorem Ipsum</span></div>
  <div class="stat" style="left:491px"><b>30</b><span>Lorem Ipsum</span></div>
  <div class="stat" style="left:577px"><b>18</b><span>Lorem Ipsum</span></div>
  <div class="stat" style="left:663px"><b>45</b><span>Lorem Ipsum</span></div>
  <div class="footer-page">PAGE | 07</div><div class="footer-copy">© 2024 Plorven Marketing | All Rights Reserved</div>
  <div class="brand"><i></i>Plorven</div>
</section>

<!-- Slide 8 -->
<section class="slide col-r row-4">
  <svg class="frame" width="765" height="430"><polygon points="0,0 648,0 620,46 0,46" fill="#e2001a"/><polygon points="660,0 765,0 765,46 634,46" fill="#3d3d3f"/><polygon points="0,46 405,46 395,58 0,58" fill="#3d3d3f"/><polygon points="0,412 590,412 610,430 0,430" fill="#e2001a"/></svg>
  <h1 class="slide-title">END SLIDE</h1>
  <p class="abs lead" style="left:0;top:89px;width:765px;text-align:center">Maximize Lead Potential with Cross-Offer Opportunities</p>
  <div class="photo" role="img" aria-label="Photo of a woman shopping online with a payment card" style="left:34px;top:130px;width:232px;height:246px;background:linear-gradient(135deg,#9a8a6a,#5e6b3e)"></div>
  <div class="photo" role="img" aria-label="Photo of hands pointing at financial charts on a screen" style="left:266px;top:130px;width:231px;height:246px;background:linear-gradient(135deg,#1e3a4f,#0f1c28)"></div>
  <div class="photo" role="img" aria-label="Photo of a hand holding a phone with floating customer reviews" style="left:497px;top:130px;width:232px;height:246px;background:linear-gradient(135deg,#e9eae8,#b9c2a6)"></div>
  <div class="footer-page">PAGE | 08</div><div class="footer-copy">© 2024 Plorven Marketing | All Rights Reserved</div>
  <div class="brand"><i></i>Plorven</div>
</section>

</div>
</body>
</html>
```